Summit Ridge Business Card

Side 1: Summit Ridge Logo (logo without Maltese cross) with industrial rope rescue related theme. Our company services - TRAINING - Fire Training, Confined Space Rescue Training, Rope Rescue training, Hazmat Training, Incident Command, EMS, Pump Operations Training. Website - summitridgeexample.com.
Side 2: Summit Ridge Fire Department Logo (logo with Maltese cross) with Firefighter related theme. Company (division) services - FIELD SERVICES - Fire Department, Stand-by Rescue, Safety, EMS, Planning. "Supporting the Emergency Response Community Since 1967"

Add contact information wherever it makes since (Name, Email, Phone).
I would like it to represent the Summit Ridge Fire Department Logo as a division not as a separate entity without saying it, possibly by depicting it in the background of Side 2 instead of being a standalone picture like the logo on Side 1.

```html
<!DOCTYPE html>
<html lang="en">
<head>
<meta charset="utf-8">
<title>Summit Ridge Business Card</title>
<link href="https://fonts.googleapis.com/css2?family=Poppins:ital,wght@0,400;0,600;0,700;1,500&display=swap" rel="stylesheet">
<style>
  :root {
    --stage: #b8b8b8;
    --red: #ff0000;
    --white: #ffffff;
    --ink: #2a2a2a;
    --black: #0d0d0d;
  }
  * { margin: 0; padding: 0; box-sizing: border-box; }
  html, body { width: 1200px; height: 1200px; overflow: hidden; }
  body {
    background: var(--stage);
    font-family: "Poppins", sans-serif;
    position: relative;
  }
  .card {
    position: absolute;
    top: 303px;
    width: 369px;
    height: 594px;
    overflow: hidden;
    text-align: center;
  }
  .card-front { left: 200px; background: var(--white); }
  .card-back { left: 600px; background: var(--red); color: var(--white); }

  .brand-dot {
    position: absolute;
    left: 50%;
    top: 70px;
    width: 64px;
    height: 64px;
    margin-left: -32px;
    border-radius: 50%;
    background: var(--red);
  }
  .brand-name {
    position: absolute;
    left: 0; right: 0;
    top: 176px;
    font-size: 34px;
    font-weight: 700;
    letter-spacing: 0.5px;
    color: var(--red);
    line-height: 1;
  }
  .section-title {
    position: absolute;
    left: 0; right: 0;
    font-weight: 700;
    line-height: 1;
  }
  .card-front .section-title { top: 284px; font-size: 32px; color: var(--red); }
  .card-back .section-title { top: 140px; font-size: 31px; color: var(--white); }

  .service-list {
    position: absolute;
    left: 0; right: 0;
    list-style: none;
    text-transform: uppercase;
  }
  .card-front .service-list {
    top: 332px;
    font-size: 16.5px;
    line-height: 21.5px;
    color: var(--ink);
  }
  .card-back .service-list {
    top: 192px;
    font-size: 20px;
    line-height: 26.8px;
    font-weight: 500;
  }

  .web-band {
    position: absolute;
    left: 0; right: 0;
    top: 504px;
    height: 71px;
    background: var(--red);
    color: var(--white);
    font-size: 17.5px;
    letter-spacing: 2px;
    line-height: 71px;
  }

  .divider {
    position: absolute;
    left: 50%;
    top: 355px;
    width: 44px;
    height: 1px;
    margin-left: -22px;
    background: var(--white);
  }
  .contact-name {
    position: absolute;
    left: 0; right: 0;
    top: 370px;
    font-size: 27px;
    font-weight: 700;
    line-height: 1;
  }
  .contact-lines {
    position: absolute;
    left: 0; right: 0;
    top: 410px;
    font-size: 17.5px;
    line-height: 22px;
  }
  .tagline-band {
    position: absolute;
    left: 0; right: 0;
    top: 506px;
    height: 70px;
    background: var(--black);
    color: var(--white);
    font-style: italic;
    font-weight: 500;
    font-size: 15.5px;
    line-height: 19px;
    padding-top: 16px;
  }
</style>
</head>
<body>
  <section class="card card-front">
    <div class="brand-dot"></div>
    <div class="brand-name">SUMMIT RIDGE</div>
    <h2 class="section-title">TRAINING</h2>
    <ul class="service-list">
      <li>Fire Training</li>
      <li>Confined Space Rescue Training</li>
      <li>Rope Rescue Training</li>
      <li>Hazmat Training</li>
      <li>Incident Command</li>
      <li>EMS</li>
      <li>Pump Operations Training</li>
    </ul>
    <div class="web-band">www.summitridgeexample.com</div>
  </section>

  <section class="card card-back">
    <h2 class="section-title">FIELD SERVICES</h2>
    <ul class="service-list">
      <li>Fire Department</li>
      <li>Stand-by Rescue</li>
      <li>Safety</li>
      <li>EMS</li>
      <li>Planning</li>
    </ul>
    <div class="divider"></div>
    <div class="contact-name">Daniel Hartley</div>
    <div class="contact-lines">
      <div>044-555 010 234</div>
      <div>info@summitridgeexample.com</div>
    </div>
    <div class="tagline-band">
      Supporting the Emergency Response<br>Community Since 1967
    </div>
  </section>
</body>
</html>
```